Creative, fresh business card design for Ripplecraft Facades

We need a fresh, creative business card design for Ripplecraft Facades. We are the manufacturer of Ripplecraft Facades in Australia. Wall panels are 2400 x 1200mm panels made from MDF and feature 3D patterns on the face of the panel. The colours to be used are green, silver/grey and white RGB
Red 187
Green 207
Blue 65.

An idea is to possibly use a watermark of one of our designs as a background (like on the "Grids" design on the left hand side of page 2 of our brochure).

Target Market(s)

Interior designers, architects, builders and home renovators

Industry/Entity Type

Business

Contact Information for Business Card

Details to go on the card are:
Our logo (attached),
Slogan: "Decorative panels for interiors and exteriors",
Contact name,
Position,
Mobile phone number,
Business address,
Business phone,
Business fax,
Website and
Email address.

I have attached a few images of our panels and our brochure for reference.

The colours of the business card should feature our logo colours which are: RGB
Red 187
Green 207
Blue 65

Requirements
Must have
• Very modern fonts and design. Some of the designs shown especially the "Prisms" design which is a popular design.
Nice to have
• Creative but simple design. Very contemporary.
Should not have
• Anything ornate or old fashioned.

```html
<!DOCTYPE html>
<html lang="en">
<head>
<meta charset="utf-8">
<title>Ripplecraft Facades — Business Card</title>
<link rel="stylesheet" href="https://fonts.googleapis.com/css2?family=Arimo:wght@400;700&display=swap">
<style>
  :root {
    --brand-green: rgb(187, 207, 65);
    --band-grey: #8d8e90;
    --text-grey: #7a7b7d;
    --white: #ffffff;
    --stage: #ececec;
    --card-shadow: 0 4px 14px rgba(0, 0, 0, 0.18);
  }
  * { box-sizing: border-box; margin: 0; padding: 0; }
  html, body { width: 1200px; height: 987px; overflow: hidden; }
  body {
    background: var(--stage);
    font-family: "Arimo", Arial, sans-serif;
    position: relative;
  }
  .card {
    position: absolute;
    left: 293px;
    width: 615px;
    height: 350px;
    box-shadow: var(--card-shadow);
    overflow: hidden;
  }
  .card--front { top: 131px; background: var(--white); }
  .card--back { top: 506px; background: var(--brand-green); }

  /* Front */
  .front-brand {
    position: absolute;
    top: 58px;
    left: 0;
    width: 100%;
    text-align: center;
  }
  .brand-lockup {
    display: inline-flex;
    align-items: center;
    gap: 12px;
  }
  .brand-mark {
    width: 34px;
    height: 34px;
    background: var(--brand-green);
  }
  .brand-name {
    font-size: 34px;
    font-weight: 700;
    color: var(--brand-green);
    letter-spacing: -0.5px;
  }
  .front-slogan {
    margin-top: 14px;
    font-size: 12px;
    line-height: 14px;
    letter-spacing: 2.4px;
    color: var(--text-grey);
  }
  .name-band {
    position: absolute;
    top: 200px;
    left: 0;
    width: 100%;
    height: 43px;
    background: var(--band-grey);
    display: flex;
    align-items: center;
    justify-content: center;
    gap: 6px;
    border-bottom: 3px solid var(--white);
    height: 46px;
  }
  .person-name {
    font-size: 20px;
    font-weight: 700;
    color: var(--brand-green);
  }
  .person-role {
    font-size: 17px;
    color: var(--white);
  }
  .contact-block {
    position: absolute;
    top: 246px;
    left: 0;
    width: 100%;
    height: 104px;
    background: var(--brand-green);
    color: var(--white);
    text-align: center;
    font-size: 16px;
    line-height: 25px;
    padding-top: 16px;
  }
  .contact-label { font-weight: 700; }

  /* Back */
  .back-brand {
    position: absolute;
    right: 40px;
    top: 168px;
    width: 200px;
    text-align: center;
    color: var(--white);
  }
  .back-brand .brand-lockup { gap: 8px; }
  .back-brand .brand-mark { width: 22px; height: 22px; background: var(--white); }
  .back-brand .brand-name { font-size: 22px; color: var(--white); letter-spacing: 0; }
  .back-slogan {
    margin-top: 12px;
    font-size: 11px;
    line-height: 13px;
    letter-spacing: 2px;
  }
  .back-web {
    margin-top: 6px;
    font-size: 15px;
  }
</style>
</head>
<body>
  <section class="card card--front" aria-label="Business card front">
    <div class="front-brand">
      <div class="brand-lockup">
        <span class="brand-mark"></span>
        <span class="brand-name">Ripplecraft Facades</span>
      </div>
      <p class="front-slogan">decorative panels for<br>interiors &amp; landscapes</p>
    </div>
    <div class="name-band">
      <span class="person-name">DANA HOLLIS -</span>
      <span class="person-role">CEO&amp;Founder</span>
    </div>
    <div class="contact-block">
      <p>4120 Kestrel Road, Geelong, Victoria 3220</p>
      <p><span class="contact-label">P :</span> (555) 214-7093&nbsp; <span class="contact-label">F :</span> (555) 382-6150</p>
      <p>dhollis@ripplecraft.com | www.ripplecraft.com</p>
    </div>
  </section>

  <section class="card card--back" aria-label="Business card back">
    <div class="back-brand">
      <div class="brand-lockup">
        <span class="brand-mark"></span>
        <span class="brand-name">Ripplecraft Facades</span>
      </div>
      <p class="back-slogan">decorative panels for<br>interiors &amp; landscapes</p>
      <p class="back-web">www.ripplecraft.com</p>
    </div>
  </section>
</body>
</html>
```